Business card for denture clinic Veltrimora

We need a new business card with our new logo. We are a denture clinic in New Zealand with our target market being 45+ years old. We would need a space on the back to write our patients next appointment on. We would space for only one appointment rather than a list. We will attach a photo showing an example of this. But of course, we would like to see your twist on this. We want it to be bold and easy to read and a good mixture of professional but modern. We have attached our logo to be used on the card.

Target Market(s)

People aged 45+ needing dentures

Industry/Entity Type

Dental

Contact Information for Business Card

We want our logo on the front and the space to write an appointment on the back. I've attached an example our our old business card showing this. We need to have the technicians details on the front.

Font styles to use
Sans Serif

Colors
0255a3
919191
fbfbfb

Requirements
Must have
• The following details:
• Liam Dorsett BDT, PGDipCDentTech Calverin
• Dental Prosthetist
• Phone numbers: 0800 47 3125
• 09 572 1394
• Email: liam@veltrimora.co.nz
• www.veltrimora.co.nz
• Address: 14 Marlow Crest Road
• Halbrook West
• Auckland 0793
Nice to have
• We would like our business cards to have more than just two colours as we want them to be more vibrant. We have uploaded an example of a business card we liked that showed this.

```html
<!DOCTYPE html>
<html lang="en">
<head>
<meta charset="utf-8">
<title>Veltrimora Business Card</title>
<link rel="stylesheet" href="https://fonts.googleapis.com/css2?family=Open+Sans:ital,wght@0,400;0,600;0,700;1,400&display=swap">
<style>
  :root {
    --brand-blue: #0270ba;
    --brand-blue-deep: #0255a3;
    --text-grey: #919191;
    --text-dark: #444444;
    --card-white: #fbfbfb;
    --field-fill: #f4f4f4;
    --backdrop: #e8e5e0;
  }
  * { margin: 0; padding: 0; box-sizing: border-box; }
  html, body {
    width: 1200px;
    height: 987px;
    overflow: hidden;
    background: var(--backdrop);
    font-family: "Open Sans", sans-serif;
  }
  .canvas { position: relative; width: 1200px; height: 987px; }

  .card {
    position: absolute;
    left: 293px;
    width: 615px;
    height: 351px;
    border-radius: 21px;
    overflow: hidden;
    box-shadow: 0 3px 8px rgba(0, 0, 0, 0.25);
  }
  .card-front { top: 130px; background: var(--card-white); }
  .card-back { top: 505px; background: var(--brand-blue); }

  .edge-tab {
    position: absolute;
    left: 0; top: 55px;
    width: 13px; height: 74px;
    background: var(--brand-blue);
    border-radius: 0 7px 7px 0;
  }

  .contact { position: absolute; left: 38px; top: 52px; }
  .person-name {
    color: var(--brand-blue);
    font-weight: 700;
    font-size: 21px;
    line-height: 26px;
  }
  .person-name .credentials { font-size: 16px; }
  .qualification {
    color: var(--brand-blue);
    font-weight: 700;
    font-size: 16px;
    line-height: 22px;
  }
  .role {
    color: var(--text-grey);
    font-size: 16px;
    line-height: 22px;
    margin-top: 3px;
  }
  .address, .reach {
    color: var(--text-dark);
    font-size: 15.5px;
    line-height: 22.5px;
    margin-left: 3px;
  }
  .address { margin-top: 7px; }
  .reach { margin-top: 10px; line-height: 23.5px; }
  .reach .label { color: var(--brand-blue); font-weight: 700; }

  .brand {
    position: absolute;
    display: flex;
    flex-direction: column;
    align-items: center;
    gap: 5px;
  }
  .brand-mark { width: 58px; height: 58px; border-radius: 3px; }
  .brand-name {
    font-weight: 600;
    font-size: 27px;
    letter-spacing: 2px;
    line-height: 30px;
  }
  .card-front .brand { left: 300px; width: 283px; top: 131px; }
  .card-front .brand-mark { background: var(--brand-blue); }
  .card-front .brand-name { color: var(--brand-blue); }

  .card-back .brand { left: 0; width: 615px; top: 52px; }
  .card-back .brand-mark { background: var(--card-white); }
  .card-back .brand-name { color: var(--card-white); }

  .appointment-title {
    position: absolute;
    top: 198px; left: 0; width: 615px;
    text-align: center;
    color: var(--card-white);
    font-weight: 600;
    font-size: 23px;
  }
  .appointment-field {
    position: absolute;
    top: 273px;
    width: 240px;
    height: 43px;
    border-radius: 22px;
    background: var(--field-fill);
    color: var(--brand-blue);
    font-style: italic;
    font-size: 17px;
    line-height: 43px;
    padding-left: 17px;
  }
  .field-date { left: 29px; }
  .field-time { left: 344px; }
</style>
</head>
<body>
<main class="canvas">

  <section class="card card-front" aria-label="Card front">
    <div class="edge-tab"></div>
    <div class="contact">
      <p class="person-name">LIAM DORSETT <span class="credentials">BDT,</span></p>
      <p class="qualification">PGDipCDentTech Calverin</p>
      <p class="role">Dental Prosthetist</p>
      <p class="address">14 Marlow Crest Road<br>Halbrook West<br>Auckland 0793</p>
      <p class="reach">
        <span class="label">P :</span> 0800 47 3125<br>
        <span class="label">C :</span> 09 572 1394<br>
        liam@veltrimora.co.nz<br>
        www.veltrimora.co.nz
      </p>
    </div>
    <div class="brand">
      <div class="brand-mark"></div>
      <p class="brand-name">VELTRIMORA</p>
    </div>
  </section>

  <section class="card card-back" aria-label="Card back">
    <div class="brand">
      <div class="brand-mark"></div>
      <p class="brand-name">VELTRIMORA</p>
    </div>
    <p class="appointment-title">Next Appointment</p>
    <div class="appointment-field field-date">date:</div>
    <div class="appointment-field field-time">time:</div>
  </section>

</main>
</body>
</html>
```